glimTo.com needs a new landing page design

We need a new landing/home page design for glimto.com. glimTo is a fun and easy design tool on the web and mobile. We want to showcase not only our online web based tool, but also our mobile apps. We want a more bright, fun and vibrant look than what we currently have.

1. glimTo logo
2. menu bar
3. header text and sub header text
4. action button
5. promote both web and mobile versions
6. include pearl and vendo market pearl store download badges

Target Market(s)

20-40 year old women

Industry/Entity Type

Design

Font styles to use
Sans Serif

Requirements
Must have
• 1. glimTo logo 2. menu bar 3. header text and sub header text 4. action button 5. promote both web and mobile versions 6. include pearl and vendo market pearl store download badges
Nice to have
• Look at other software design landing pages from Drafly, Orvix, Etc.

```html
<!DOCTYPE html>
<html lang="en">
<head>
<meta charset="utf-8">
<title>glimTo – Easily Create Anything You Can Imagine</title>
<link href="https://fonts.googleapis.com/css2?family=Montserrat:wght@400;500;600;700;800&family=Mulish:wght@400;600;700&family=Parisienne&display=swap" rel="stylesheet">
<style>
:root{
  --orange:#f7931e;
  --green:#19a974;
  --teal:#0d5a73;
  --blue:#1c7fd6;
  --ink:#1d1d1f;
  --dark:#1a1a1a;
  --darker:#121212;
  --nav:#262626;
  --panel:#23252b;
  --grey-bg:#ebebeb;
  --white:#fff;
}
*{margin:0;padding:0;box-sizing:border-box}
html,body{width:1200px;height:4873px;overflow:hidden}
body{font-family:"Mulish",sans-serif;color:var(--ink);background:var(--white);position:relative}
.sec{position:absolute;left:0;width:1200px;overflow:hidden}
.abs{position:absolute}
.script{font-family:"Parisienne",cursive;color:var(--orange)}
.h-cap{font-family:"Montserrat",sans-serif;font-weight:700;text-transform:uppercase;letter-spacing:.5px}
.btn{position:absolute;display:flex;align-items:center;justify-content:center;gap:6px;font-family:"Montserrat",sans-serif;font-weight:700;font-size:11px;letter-spacing:.6px;text-transform:uppercase;color:var(--white)}
.btn-orange{background:var(--orange)}
.btn-green{background:var(--green)}
.btn-outline{border:2px solid var(--orange);color:var(--orange)}
.dot{display:inline-block;width:8px;height:8px;border-radius:50%;background:currentColor;position:relative}
.dot::after{content:"";position:absolute;left:2px;top:2px;border-left:4px solid var(--dot-fill,#000);border-top:2px solid transparent;border-bottom:2px solid transparent}
.logo{font-family:"Montserrat",sans-serif;font-weight:700;color:var(--white)}
.panel{background:var(--panel);border-radius:6px;box-shadow:0 6px 14px rgba(0,0,0,.25)}

/* nav */
.nav{top:0;height:70px;background:var(--nav)}
.nav .logo{left:170px;top:14px;font-size:30px}
.nav-menu{left:460px;top:24px;font-size:13px;color:var(--white);font-family:"Montserrat",sans-serif}
.nav-menu span{position:absolute;white-space:nowrap}

/* hero */
.hero{top:70px;height:521px}
.hero-photo{position:absolute;inset:0;background:
  radial-gradient(ellipse 260px 300px at 870px 220px,rgba(230,232,226,.55),transparent 70%),
  radial-gradient(ellipse 200px 260px at 1000px 380px,rgba(214,170,150,.35),transparent 70%),
  linear-gradient(100deg,#3a3937 0%,#5e5d59 40%,#8f948e 68%,#b9beb8 100%)}
.hero-tag{left:176px;top:172px;font-size:46px;color:var(--white)}
.hero-title{left:176px;top:238px;font-size:50px;font-weight:800;color:var(--white);font-family:"Montserrat",sans-serif}
.hero-arrow{width:57px;height:97px;top:206px;background:rgba(30,30,30,.8);display:flex;align-items:center;justify-content:center}

/* features */
.features{top:591px;height:515px;background:var(--dark)}
.feat{position:absolute;top:87px;width:269px;text-align:center;color:var(--white)}
.feat-img{position:relative;height:189px;outline:1px solid #1fa39a;outline-offset:6px}
.feat h3{font-family:"Montserrat",sans-serif;font-size:13px;font-weight:700;margin-top:26px;text-transform:uppercase}
.feat p{font-size:12px;line-height:20px;color:#d6d6d6;margin:18px auto 0;width:240px}
.feat .btn{position:relative;margin:18px auto 0;width:101px;height:29px;--dot-fill:var(--dark)}

/* create */
.create{top:1106px;height:522px;background:var(--white)}
.toolbar{left:163px;top:-18px;width:91px;height:158px}
.create-tag{width:1200px;text-align:center;top:50px;font-size:28px}
.create-title{width:1200px;text-align:center;top:98px;font-size:33px}
.create-sub{width:1200px;text-align:center;top:157px;font-size:13px;color:#333}
.pro{display:inline-block;background:var(--blue);color:#fff;font-size:9px;font-weight:700;border-radius:50%;padding:7px 4px;vertical-align:middle}
.tool{position:absolute;top:210px;width:260px;text-align:center}
.tool svg{display:block;margin:0 auto}
.tool h3{font-family:"Montserrat",sans-serif;font-weight:500;font-size:15px;margin-top:14px;text-transform:uppercase}
.tool p{font-size:12px;line-height:20px;color:#444;margin-top:12px}

/* subscription */
.sub{top:1628px;height:333px;background:var(--teal)}
.sub-tag{left:170px;top:86px;display:flex;align-items:flex-start;gap:6px}
.sub-tag span{font-size:30px;line-height:40px}
.sub-pro{background:var(--orange);color:#fff;font-size:10px;font-weight:700;padding:1px 5px;margin-top:2px;font-family:"Montserrat",sans-serif}
.sub-title{left:170px;top:140px;font-size:30px;color:var(--white)}
.sub-text{left:719px;top:96px;width:320px;font-size:13px;line-height:22px;color:#e8f1f4}

/* app */
.app{top:1961px;height:689px;background:var(--white)}
.app-palette{left:850px;top:-23px;width:132px;height:88px}
.app-title{left:172px;top:120px;font-size:34px;font-weight:800}
.app-sub{left:172px;top:168px;font-size:13px;color:#444}
.perk{position:absolute;left:172px;display:flex;gap:22px;align-items:flex-start}
.perk h4{font-family:"Montserrat",sans-serif;font-weight:700;font-size:15px;line-height:20px}
.perk p{font-size:12px;color:#555;margin-top:4px}
.badge{position:absolute;top:521px;height:45px;background:#000;border-radius:6px;color:#fff;display:flex;align-items:center;gap:9px;padding:0 10px;white-space:nowrap}
.badge small{display:block;font-size:8px;text-transform:uppercase;letter-spacing:.3px}
.badge b{display:block;font-size:15px;font-weight:600;line-height:18px}
.badge i{width:20px;height:20px;background:#fff;border-radius:3px;display:block;flex:none}
.phone{left:660px;top:106px;width:290px;height:479px;border-radius:40px;background:#1b1b1d;transform:rotate(12deg);padding:12px}
.phone-screen{width:100%;height:100%;border-radius:30px;background:linear-gradient(180deg,#4f3631 0%,#8a5e4a 25%,#6d4b3e 45%,#f1f0ee 46%,#fafafa 85%,#e9e9e9 100%)}
.phone-shadow{left:640px;top:600px;width:340px;height:40px;border-radius:50%;background:radial-gradient(ellipse,rgba(0,0,0,.18),transparent 70%)}

/* why */
.why{top:2650px;height:572px;background:linear-gradient(90deg,#1e78cc,#2390e3)}
.why-title{width:1200px;text-align:center;top:74px;font-size:34px;color:#fff}
.why-sub{width:1200px;text-align:center;top:120px;font-size:14px;line-height:24px;color:#fff}
.monitor{left:174px;top:176px;width:400px;height:386px}
.why-lead{left:611px;top:202px;font-size:13px;color:#fff}
.point{position:absolute;left:611px;display:flex;gap:14px;color:#fff}
.point .ic{width:61px;height:61px;border-radius:50%;background:var(--orange);flex:none;display:flex;align-items:center;justify-content:center}
.point h4{font-family:"Montserrat",sans-serif;font-weight:700;font-size:16px;margin-top:4px}
.point p{font-size:12px;margin-top:6px;color:#e6f1fb}
.side-tools{left:1070px;top:521px;width:40px;height:185px;border-radius:3px}

/* meme */
.meme{top:3222px;height:504px;background:var(--white)}
.meme-art{left:120px;top:45px;width:400px;height:418px;border-radius:50%;background:
  radial-gradient(circle at 50% 42%,#f06aa6 0 22%,transparent 40%),
  radial-gradient(circle at 50% 45%,#3ec6c0 0%,#1ea6a6 60%,#0e8b8e 100%)}
.meme-tag{left:577px;top:82px;font-size:28px}
.meme-title{left:577px;top:122px;font-size:34px;font-weight:800}
.meme-text{left:577px;top:172px;width:445px;font-size:13px;line-height:24px;color:#333}
.meme-list{left:579px;top:262px;list-style:none;font-size:15px}
.meme-list li{display:flex;align-items:center;gap:10px;height:40px}
.meme-list li::before{content:"";width:14px;height:14px;border-radius:50%;background:var(--teal)}

/* cover */
.cover{top:3726px;height:458px;background:var(--grey-bg)}
.cover-tag{width:1200px;text-align:center;top:70px;font-size:28px}
.cover-title{width:1200px;text-align:center;top:108px;font-size:34px;font-weight:800}
.card{position:absolute;top:168px;width:269px;height:191px;background:#fff;box-shadow:0 4px 12px rgba(0,0,0,.12)}
.card-head{height:66px;display:flex;align-items:center;justify-content:center;color:#fff;font-family:"Montserrat",sans-serif;font-weight:700;font-size:16px}
.card-shot{height:125px}
.cover-arrow{top:246px;width:42px;height:42px;border-radius:50%;background:#8a8a8a;display:flex;align-items:center;justify-content:center}

/* stats */
.stats{top:4184px;height:274px;background:var(--dark)}
.stat{position:absolute;top:81px;width:191px;height:112px;border:2px solid #fff;display:flex;align-items:center;gap:14px;padding-left:14px;color:#fff}
.stat .ic{width:54px;height:54px;flex:none}
.stat h5{font-family:"Montserrat",sans-serif;font-weight:700;font-size:12px}
.stat span{font-size:15px;display:block;margin-top:4px}

/* cta */
.cta{top:4458px;height:123px;background:#161616}
.cta-text{left:257px;top:45px;font-family:"Montserrat",sans-serif;font-size:29px;color:#fff}
.cta-text b{font-weight:800}

/* footer */
.footer{top:4581px;height:292px;background:var(--darker);color:#bdbdbd}
.footer .logo{left:172px;top:30px;font-size:40px}
.foot-about{left:172px;top:104px;width:260px;font-size:12px;line-height:21px}
.foot-about a,.copy a{color:var(--orange);text-decoration:none}
.copy{left:172px;top:232px;font-size:11px}
.foot-col{top:48px;font-size:12px}
.foot-col h6{font-family:"Montserrat",sans-serif;font-weight:700;font-size:12px;color:#fff;letter-spacing:.5px;margin-bottom:18px}
.foot-col li{list-style:none;line-height:16px;margin-bottom:16px}
</style>
</head>
<body>

<header class="sec nav">
  <div class="abs logo">glimTo</div>
  <nav class="abs nav-menu" aria-label="Main">
    <span style="left:0">Edit</span>
    <span style="left:62px">Collage</span>
    <span style="left:140px">Design</span>
    <span style="left:218px">Touch Up</span>
    <span style="left:303px">More</span>
  </nav>
  <div class="btn btn-orange" style="left:825px;top:19px;width:97px;height:30px;font-weight:600;text-transform:none;font-size:13px">Login</div>
  <div class="btn btn-green" style="left:931px;top:19px;width:95px;height:30px;font-weight:600;text-transform:none;font-size:13px">Signup</div>
</header>

<section class="sec hero">
  <div class="hero-photo" role="img" aria-label="Hand holding a phone editing a photo of a woman sitting outdoors, with filter and slider controls"></div>
  <div class="abs script hero-tag">Easily Create Anything</div>
  <h1 class="abs hero-title">YOU CAN IMAGINE</h1>
  <div class="btn btn-orange" style="left:176px;top:326px;width:127px;height:38px">Get Started</div>
  <div class="abs hero-arrow" style="left:0"><svg width="22" height="40" viewBox="0 0 22 40"><path d="M18 4 4 20l14 16" fill="none" stroke="#fff" stroke-width="2"/></svg></div>
  <div class="abs hero-arrow" style="left:1143px"><svg width="22" height="40" viewBox="0 0 22 40"><path d="M4 4l14 16L4 36" fill="none" stroke="#fff" stroke-width="2"/></svg></div>
</section>

<section class="sec features">
  <div class="feat" style="left:172px">
    <div class="feat-img" role="img" aria-label="Collage of portraits with text, borders and stickers on a yellow background" style="background:radial-gradient(circle at 30% 40%,#c98f5e 0 14%,transparent 30%),radial-gradient(circle at 75% 70%,#b9784e 0 12%,transparent 28%),linear-gradient(135deg,#e2cb1e,#b9b12a 55%,#4f7a2e)"></div>
    <h3>Add Text, Borders &amp; Stickers</h3>
    <p>A vast array of fonts, graphics and other goodies for your photo editing pleasure.</p>
    <div class="btn btn-outline">Try It <i class="dot"></i></div>
  </div>
  <div class="feat" style="left:466px">
    <div class="feat-img" role="img" aria-label="Black and white portrait with a paint splash effect" style="background:radial-gradient(circle at 55% 45%,#4a4a4a 0 18%,transparent 40%),linear-gradient(135deg,#f0f0f0,#9a9a9a 50%,#3a3a3a)"></div>
    <h3>Basic &amp; Advanced Tools</h3>
    <p>You don't need to be a Pixelforge expert to get up and running quickly with glimTo.</p>
    <div class="btn btn-outline">Try It <i class="dot"></i></div>
  </div>
  <div class="feat" style="left:759px">
    <div class="feat-img" role="img" aria-label="Soft pastel photo of a woman reading a book" style="background:radial-gradient(circle at 60% 50%,#6d5142 0 12%,transparent 30%),linear-gradient(135deg,#f6f1ec,#dccdc0 55%,#b8a293)"></div>
    <h3>Fab Filters &amp; Effects</h3>
    <p>With a single click, transform your boring photo into a masterpiece.</p>
    <div class="btn btn-outline">Try It <i class="dot"></i></div>
  </div>
</section>

<section class="sec create" style="overflow:visible">
  <svg class="abs toolbar panel" viewBox="0 0 91 158" aria-label="Layer toolbar with opacity control">
    <g fill="none" stroke="#fff" stroke-width="2">
      <path d="M16 30h12M18 30v12h8V30M20 26h4"/>
      <rect x="60" y="30" width="12" height="10" rx="1"/><path d="M62 30v-4a4 4 0 0 1 8 0v4"/>
      <rect x="16" y="64" width="11" height="13"/><path d="M19 64v-3h11v13h-3"/>
      <rect x="60" y="62" width="10" height="10"/><rect x="64" y="66" width="10" height="10" fill="#fff"/>
      <rect x="16" y="98" width="10" height="10"/><rect x="20" y="102" width="10" height="10"/>
    </g>
    <text x="14" y="134" fill="#fff" font-family="Mulish,sans-serif" font-size="12">Opacity</text>
    <rect x="72" y="144" width="10" height="8" fill="#9aa"/>
  </svg>
  <div class="abs script create-tag">Easily Create</div>
  <h2 class="abs h-cap create-title">Anything You Can Imagine</h2>
  <p class="abs create-sub">Try the FREE version or upgrade to glimTo glimTo<span class="pro">PRO</span> photo editor - FREE 7 Day Trial</p>

  <div class="tool" style="left:167px">
    <svg width="70" height="66" viewBox="0 0 70 66"><rect x="8" y="8" width="46" height="40" fill="none" stroke="#222" stroke-width="2" stroke-dasharray="4 3"/><path d="M14 42l12-14 8 9 6-6 10 11z" fill="#7bc043"/><circle cx="40" cy="20" r="4" fill="#f7931e"/><path d="M50 44l14 14-5 1 3 6-3 1-3-6-4 3z" fill="#222"/></svg>
    <h3>Photo Editor</h3>
    <p>Editing photos with glimTo is simple, fun and perfect for any skill level. Everyone wins with glimTo!</p>
  </div>
  <div class="tool" style="left:470px">
    <svg width="70" height="66" viewBox="0 0 70 66"><rect x="14" y="6" width="42" height="52" fill="#fff" stroke="#222" stroke-width="2"/><rect x="19" y="11" width="15" height="20" fill="#3aa3e3"/><rect x="37" y="11" width="14" height="12" fill="#e94b8a"/><rect x="37" y="26" width="14" height="26" fill="#7bc043"/><rect x="19" y="34" width="15" height="18" fill="#8e5cc9"/></svg>
    <h3>Collage Maker</h3>
    <p>Craft the perfect collage with glimTo's easy-to-use Collage Maker. Choose from over 1000 designs.</p>
  </div>
  <div class="tool" style="left:771px">
    <svg width="70" height="66" viewBox="0 0 70 66"><path d="M12 12l46 42M58 12 12 54" stroke="#e94b3c" stroke-width="6"/><circle cx="35" cy="33" r="8" fill="#3aa3e3"/><circle cx="14" cy="14" r="5" fill="#f7931e"/><circle cx="56" cy="52" r="5" fill="#7bc043"/></svg>
    <h3>Design Tool</h3>
    <p>Be careful... Our Design Tool is utterly addictive! Make cards, flyers, or the perfect social media post.</p>
  </div>

  <div class="btn btn-orange" style="left:172px;top:405px;width:123px;height:32px;--dot-fill:var(--orange)">Try It <i class="dot"></i></div>
  <div class="btn btn-green" style="left:301px;top:405px;width:123px;height:32px;--dot-fill:var(--green)">Read More <i class="dot"></i></div>
  <div class="btn btn-orange" style="left:473px;top:405px;width:123px;height:32px;--dot-fill:var(--orange)">Try It <i class="dot"></i></div>
  <div class="btn btn-green" style="left:602px;top:405px;width:123px;height:32px;--dot-fill:var(--green)">Read More <i class="dot"></i></div>
  <div class="btn btn-orange" style="left:776px;top:405px;width:123px;height:32px;--dot-fill:var(--orange)">Try It <i class="dot"></i></div>
  <div class="btn btn-green" style="left:905px;top:405px;width:123px;height:32px;--dot-fill:var(--green)">Read More <i class="dot"></i></div>
</section>

<section class="sec sub">
  <div class="abs sub-tag"><span class="script">Try glimTo glimTo</span><b class="sub-pro">PRO</b></div>
  <h2 class="abs h-cap sub-title">Subscription Free for 7 Days</h2>
  <p class="abs sub-text">Get the most out of glimTo with glimTo PRO. You get loads of extra fonts, stickers, and filters. Zap all those annoying ads, and save your work at the highest quality.</p>
  <div class="btn btn-outline" style="left:719px;top:206px;width:139px;height:34px;--dot-fill:var(--teal)">Learn More <i class="dot"></i></div>
</section>

<section class="sec app" style="overflow:visible">
  <svg class="abs app-palette panel" viewBox="0 0 132 88" aria-label="Colour and layer tool panel">
    <circle cx="8" cy="7" r="2" fill="#e94b3c"/><circle cx="15" cy="7" r="2" fill="#f7c948"/><circle cx="22" cy="7" r="2" fill="#7bc043"/>
    <circle cx="20" cy="32" r="11" fill="#e94b8a"/><path d="M20 21a11 11 0 0 1 11 11H20z" fill="#3aa3e3"/><path d="M9 32a11 11 0 0 1 11-11v11z" fill="#f7c948"/>
    <rect x="38" y="20" width="34" height="24" rx="2" fill="#7e57c2"/><path d="M40 42l10-12 8 8 6-5 6 9z" fill="#3aa3e3"/>
    <g fill="#cfd3da"><rect x="10" y="54" width="14" height="10" rx="2"/><rect x="28" y="54" width="14" height="10" rx="2"/><rect x="46" y="54" width="14" height="10" rx="2"/><rect x="64" y="54" width="14" height="10" rx="2"/><rect x="10" y="68" width="14" height="10" rx="2"/><rect x="28" y="68" width="14" height="10" rx="2"/><rect x="46" y="68" width="14" height="10" rx="2"/><rect x="64" y="68" width="14" height="10" rx="2"/></g>
    <g stroke="#cfd3da" stroke-width="2"><path d="M88 24h34M88 38h34M88 52h34M88 66h34"/></g>
    <g fill="#fff"><circle cx="110" cy="24" r="3"/><circle cx="96" cy="38" r="3"/><circle cx="114" cy="52" r="3"/><circle cx="100" cy="66" r="3"/></g>
  </svg>
  <h2 class="abs h-cap app-title">Get the glimTo App</h2>
  <p class="abs app-sub">Don't miss glimTo on your phone or tablet!</p>

  <div class="perk" style="top:216px">
    <svg width="65" height="66" viewBox="0 0 65 66"><path d="M32.5 2 61 18v30L32.5 64 4 48V18z" fill="var(--blue)"/><path d="M22 44V30h6l6-10c3 0 4 2 3 5l-2 5h8c2 0 3 2 2 4l-3 9c-1 2-2 3-4 3H22z" fill="#f7c948"/></svg>
    <div><h4>Enjoy the same features as the website</h4><p>Edit photos, make collages, make memes and more.</p></div>
  </div>
  <div class="perk" style="top:309px">
    <svg width="65" height="66" viewBox="0 0 65 66"><path d="M32.5 2 61 18v30L32.5 64 4 48V18z" fill="var(--orange)"/><path d="M20 22h26v22H20z" fill="#f7c948"/><path d="M26 28h14v16H26z" fill="#7bc043"/></svg>
    <div><h4>Over 10 million downloads!</h4><p>Check out our reviews, our users are loving his app.</p></div>
  </div>
  <div class="perk" style="top:409px">
    <svg width="65" height="66" viewBox="0 0 65 66"><path d="M32.5 2 61 18v30L32.5 64 4 48V18z" fill="var(--green)"/><text x="32.5" y="42" text-anchor="middle" font-family="serif" font-size="24" fill="#f7c948">Aa</text></svg>
    <div><h4>More fonts and stickers than any other<br>mobile app.</h4><p>Seriously, check it out. You won't be bored a.</p></div>
  </div>

  <div class="badge" style="left:172px;width:155px"><i></i><div><small>Get it on</small><b>vendo market</b></div></div>
  <div class="badge" style="left:337px;width:159px"><i style="border-radius:50%"></i><div><small>Available on the</small><b>pearl store</b></div></div>

  <div class="abs phone-shadow"></div>
  <div class="abs phone"><div class="phone-screen" role="img" aria-label="Mobile app screen showing an outdoor lifestyle design template with editing tools"></div></div>
</section>

<section class="sec why" style="overflow:visible">
  <h2 class="abs h-cap why-title">Why Choose Us</h2>
  <p class="abs why-sub">You don't need to be a Pixelforge expert to have fun editing your digital photos.<br>With glimTo you can start right away without ever reading a manual or taking a class.</p>
  <div class="abs monitor">
    <svg width="400" height="386" viewBox="0 0 400 386" role="img" aria-label="Desktop monitor showing the glimTo editor with an adopt a pet poster design">
      <defs><linearGradient id="poster" x1="0" y1="0" x2="0" y2="1"><stop offset="0" stop-color="#a02fd0"/><stop offset="1" stop-color="#e05ad8"/></linearGradient></defs>
      <rect x="0" y="0" width="400" height="290" rx="8" fill="#1c1d22"/>
      <rect x="12" y="12" width="376" height="266" fill="#2a2c33"/>
      <rect x="12" y="12" width="100" height="266" fill="#22242a"/>
      <g fill="#3aa3e3"><circle cx="24" cy="40" r="4"/><circle cx="24" cy="60" r="4" fill="#f7931e"/><circle cx="24" cy="80" r="4" fill="#7bc043"/><circle cx="24" cy="100" r="4" fill="#e94b3c"/><circle cx="24" cy="120" r="4" fill="#8e5cc9"/></g>
      <g fill="#4a4d56"><rect x="36" y="36" width="66" height="8"/><rect x="36" y="56" width="56" height="8"/><rect x="36" y="76" width="62" height="8"/></g>
      <rect x="150" y="30" width="190" height="232" fill="url(#poster)"/>
      <rect x="170" y="170" width="150" height="80" fill="#f0d9e6" opacity=".6"/>
      <path d="M0 290h400v20H0z" fill="#c9cbd0"/>
      <path d="M170 310h60l10 60h-80z" fill="#b9bbc0"/>
      <rect x="110" y="368" width="180" height="12" rx="4" fill="#a9abb0"/>
    </svg>
  </div>
  <p class="abs why-lead">glimTo is free to use with no registration required!</p>
  <div class="point" style="top:237px"><div class="ic"><svg width="28" height="28" viewBox="0 0 28 28"><path d="M14 3 25 9v10L14 25 3 19V9z" fill="#8e5cc9"/></svg></div><div><h4>Easy to Use</h4><p>Seriously! Become an expert the first time you use it.</p></div></div>
  <div class="point" style="top:313px"><div class="ic"><svg width="28" height="28" viewBox="0 0 28 28"><circle cx="14" cy="14" r="10" fill="#f7c948"/><path d="M9 14h10M14 9v10" stroke="#e94b3c" stroke-width="3"/></svg></div><div><h4>Packed Full Of Free Content</h4><p>1000's of colorful stickers, sweet fonts, and amazing filters!</p></div></div>
  <div class="point" style="top:388px"><div class="ic" style="background:var(--green)"><svg width="28" height="28" viewBox="0 0 28 28"><path d="M6 22 18 6l4 4-12 16z" fill="#fff"/><circle cx="22" cy="22" r="3" fill="#f7c948"/></svg></div><div><h4>It Really is Fun!</h4><p>Once you start, its hard to stop... you have been warned</p></div></div>
  <div class="btn btn-orange" style="left:611px;top:475px;width:142px;height:35px;--dot-fill:var(--orange)">Start Editing <i class="dot"></i></div>
  <svg class="abs side-tools panel" viewBox="0 0 40 185" aria-label="Vertical drawing tools palette">
    <g fill="none" stroke="#cfd3da" stroke-width="1.6">
      <path d="M10 12l6 6-3 1M26 10l4 8"/>
      <path d="M9 36l7-7 2 2-7 7zM25 38l6-8"/>
      <path d="M10 52h8M14 52v10M26 54l6 6"/>
      <rect x="9" y="72" width="8" height="8"/><path d="M25 80l7-8"/>
      <path d="M9 96l5-5 4 4-5 5zM25 92l6 6-6 2z"/>
      <rect x="9" y="110" width="8" height="8"/><circle cx="28" cy="114" r="4"/>
    </g>
    <g fill="#cfd3da"><circle cx="16" cy="134" r="1.5"/><circle cx="20" cy="134" r="1.5"/><circle cx="24" cy="134" r="1.5"/></g>
    <rect x="12" y="150" width="12" height="12" fill="#fff"/><rect x="18" y="156" width="12" height="12" fill="#e94b3c"/>
  </svg>
</section>

<section class="sec meme">
  <div class="abs meme-art" role="img" aria-label="Pop-art illustration of a woman with pink hair and heart sunglasses on a teal circle"></div>
  <div class="abs script meme-tag">Meme maker, cut-out tool &amp;</div>
  <h2 class="abs h-cap meme-title">Design Your Own Emoji!</h2>
  <p class="abs meme-text">The fun doesn't stop with eding photos and making collages. Use glimTo to make hilarious MEME's, design custom emoji, and slice and dice photos with the Cut-Out Tool.</p>
  <ul class="abs meme-list">
    <li>MEME Maker &amp; MEME Stickers</li>
    <li>Cut-Out Tool</li>
    <li>Emoji Maker - Design your own emoji</li>
  </ul>
  <div class="btn btn-orange" style="left:579px;top:390px;width:114px;height:34px;--dot-fill:var(--orange)">Try It <i class="dot"></i></div>
</section>

<section class="sec cover">
  <div class="abs script cover-tag">Social media</div>
  <h2 class="abs h-cap cover-title">Cover Photo Editor!</h2>
  <div class="card" style="left:172px"><div class="card-head" style="background:#3b5b98">Linkora</div><div class="card-shot" role="img" aria-label="Profile page with a landscape cover photo" style="background:linear-gradient(180deg,#c6d3e0,#8fa08e 60%,#5e6f55)"></div></div>
  <div class="card" style="left:466px"><div class="card-head" style="background:#3ca6e6">Chirply</div><div class="card-shot" role="img" aria-label="Profile page with a bamboo forest cover photo" style="background:linear-gradient(180deg,#7fa86a,#3f6b2f 60%,#2b4a22)"></div></div>
  <div class="card" style="left:759px"><div class="card-head" style="background:#d9302a">Streamo</div><div class="card-shot" role="img" aria-label="Channel page with a pink abstract banner and city at night" style="background:linear-gradient(180deg,#f8f8f8 0%,#f06a9b 30%,#2a2f55 75%)"></div></div>
  <div class="abs cover-arrow" style="left:155px"><svg width="14" height="20" viewBox="0 0 14 20"><path d="M11 2 3 10l8 8" fill="none" stroke="#fff" stroke-width="2"/></svg></div>
  <div class="abs cover-arrow" style="left:1011px"><svg width="14" height="20" viewBox="0 0 14 20"><path d="M3 2l8 8-8 8" fill="none" stroke="#fff" stroke-width="2"/></svg></div>
</section>

<section class="sec stats">
  <div class="stat" style="left:172px"><svg class="ic" viewBox="0 0 54 54"><circle cx="18" cy="20" r="9" fill="#f7931e"/><circle cx="36" cy="20" r="9" fill="#e94b3c"/><path d="M4 48c0-10 6-16 14-16s14 6 14 16zM22 48c0-10 6-16 14-16s14 6 14 16z" fill="#3aa3e3"/></svg><div><h5>USERS</h5><span>59103696</span></div></div>
  <div class="stat" style="left:394px"><svg class="ic" viewBox="0 0 54 54"><rect x="4" y="6" width="46" height="36" rx="8" fill="#e94b3c"/><path d="M16 42l-4 10 12-10z" fill="#e94b3c"/><path d="M27 34c-8-6-12-10-12-14a6 6 0 0 1 12-2 6 6 0 0 1 12 2c0 4-4 8-12 14z" fill="#fff"/></svg><div><h5>LIKES</h5><span>8978124</span></div></div>
  <div class="stat" style="left:615px"><svg class="ic" viewBox="0 0 54 54"><circle cx="27" cy="27" r="24" fill="#f15a24"/><path d="M27 12v20M19 24l8 8 8-8M16 38h22" fill="none" stroke="#fff" stroke-width="4"/></svg><div><h5>DOWNLOADS</h5><span>10345432</span></div></div>
  <div class="stat" style="left:837px"><svg class="ic" viewBox="0 0 54 54"><rect x="4" y="8" width="46" height="38" rx="3" fill="#3aa3e3"/><path d="M8 42l12-14 8 8 6-6 12 12z" fill="#7bc043"/><circle cx="38" cy="18" r="5" fill="#f7c948"/></svg><div><h5>IMAGES</h5><span>351404370</span></div></div>
</section>

<section class="sec cta">
  <p class="abs cta-text"><b>FREE,</b> NO REGISTRATION REQUIRED</p>
  <div class="btn btn-outline" style="left:818px;top:43px;width:129px;height:40px;--dot-fill:#161616">Try It <i class="dot"></i></div>
</section>

<footer class="sec footer">
  <div class="abs logo">glimTo</div>
  <p class="abs foot-about">Thank you for visiting our site. Our goal is to provide a fun and easy tool that helps people be creative and express themselves. <a>Make a glimTo</a></p>
  <p class="abs copy">© 2022 <a>glimTo</a>. All right reserved</p>
  <div class="abs foot-col" style="left:541px;width:260px">
    <h6>LATEST FROM BLOG</h6>
    <ul><li>5 Easy Steps to Zombify Yourself</li><li>Halloween Party Planning Made Easy</li><li>Eat, Drink &amp; be Thankful - Free<br>Thanksgiving Printables</li></ul>
  </div>
  <div class="abs foot-col" style="left:928px">
    <h6>USEFUL LINKS</h6>
    <ul><li>Help</li><li>Contact</li><li>Privacy &amp; terms</li><li>glimTo pro</li><li>Thank you</li></ul>
  </div>
</footer>

</body>
</html>
```